Hot Consulting firm collateral upgrade

We need a stationary design for our Oakland based consulting company called Talvora. We provide consulting expertise in KLT compliance for Medical Device, Pharmaceutical, and Biotech companies. We will be using the stationary for all of our marketing collateral. We want the design to convey professionalism and quality. You can find our company color scheme from our website talvora-advisory.com. I have included a copy of our current stationary that needs an upgrade.
Target Market(s)
Medical Device, Pharma, and Biotech companies
Industry/Entity Type
It Company
Look and feel

```html
<!DOCTYPE html>
<html lang="en">
<head>
<meta charset="utf-8">
<title>Talvora Stationery Set</title>
<link rel="stylesheet" href="https://fonts.googleapis.com/css2?family=Questrial&display=swap">
<style>
  :root {
    --brand-blue: #0b529e;
    --brand-blue-dark: #084486;
    --paper: #f2f2f2;
    --ink: #4a4a4a;
    --ink-soft: #6a6a6a;
    --band-grey: #5a5a5a;
    --backdrop: #d2d2d2;
    --wordmark: #4d4d4d;
  }
  * { box-sizing: border-box; margin: 0; padding: 0; }
  html, body { width: 1200px; height: 1000px; overflow: hidden; }
  body {
    background: var(--backdrop);
    font-family: "Questrial", "Century Gothic", sans-serif;
    color: var(--ink);
    position: relative;
  }
  .piece { position: absolute; }

  .wordmark { font-family: "Questrial", sans-serif; letter-spacing: 0.5px; line-height: 1; }

  /* Folder */
  .folder {
    left: 152px; top: 41px; width: 430px; height: 559px;
    background: linear-gradient(180deg, var(--brand-blue) 0%, var(--brand-blue-dark) 100%);
    border-radius: 4px;
  }
  .folder-spine { position: absolute; left: 24px; top: 0; bottom: 0; width: 1px; background: rgba(0,0,0,0.18); }
  .folder .wordmark { position: absolute; left: 180px; top: 92px; font-size: 40px; color: #fff; }

  /* Letterhead */
  .letterhead { left: 616px; top: 61px; width: 416px; height: 539px; background: var(--paper); }
  .letterhead .wordmark { position: absolute; left: 26px; top: 44px; font-size: 27px; color: var(--wordmark); }
  .letter-body { position: absolute; left: 26px; top: 176px; width: 366px; font-size: 6.3px; line-height: 1.32; color: var(--ink-soft); }
  .letter-body p { margin-bottom: 7px; }
  .letter-body .salutation, .letter-body .sign-name { color: var(--ink); font-weight: bold; }
  .signature { position: absolute; left: 72px; top: 340px; width: 90px; height: 30px; background: linear-gradient(90deg, rgba(60,80,160,0.15), rgba(60,80,160,0.05)); }
  .footer-contacts { position: absolute; left: 26px; top: 512px; right: 26px; display: flex; font-size: 6.3px; color: var(--ink-soft); }
  .footer-contacts span { display: inline-flex; align-items: center; margin-right: 10px; }
  .footer-contacts .copyright { margin-left: auto; margin-right: 0; }
  .icon { width: 7px; height: 7px; margin-right: 3px; fill: var(--brand-blue); }

  .band { position: absolute; left: 0; right: 0; bottom: 0; height: 10px; display: flex; }
  .band-grey { background: var(--band-grey); }
  .band-blue { background: var(--brand-blue); flex: 1; }

  /* Envelope front */
  .envelope-front { left: 117px; top: 629px; width: 465px; height: 202px; background: var(--paper); }
  .envelope-front .wordmark { position: absolute; left: 26px; top: 36px; font-size: 25px; color: var(--wordmark); }
  .return-address { position: absolute; left: 26px; top: 64px; font-size: 6.3px; line-height: 1.35; color: var(--ink-soft); }

  /* Envelope back */
  .envelope-back { left: 616px; top: 629px; width: 465px; height: 202px; background: var(--paper); }
  .envelope-back svg { position: absolute; left: 0; top: 0; }
  .envelope-back .wordmark { position: absolute; left: 0; right: 0; top: 35px; text-align: center; font-size: 12px; color: #fff; }

  /* Business cards */
  .card-front { left: 410px; top: 860px; width: 170px; height: 98px; background: var(--brand-blue); }
  .card-front .wordmark { position: absolute; left: 16px; top: 28px; font-size: 16px; color: #fff; }
  .card-front .card-url { position: absolute; left: 16px; top: 84px; font-size: 5px; color: rgba(255,255,255,0.8); }

  .card-back { left: 616px; top: 860px; width: 172px; height: 98px; background: var(--paper); }
  .card-back .wordmark { position: absolute; right: 12px; top: 18px; font-size: 16px; color: var(--wordmark); }
  .card-name { position: absolute; left: 10px; top: 19px; font-size: 5.5px; color: var(--brand-blue); font-weight: bold; letter-spacing: 0.3px; }
  .card-role { position: absolute; left: 10px; top: 26px; font-size: 4.5px; color: var(--ink-soft); }
  .card-contacts { position: absolute; left: 10px; top: 69px; font-size: 4.3px; line-height: 1.45; color: var(--ink-soft); }
  .card-contacts .icon { width: 4.5px; height: 4.5px; margin-right: 2px; }
  .card-address { position: absolute; right: 12px; top: 69px; text-align: right; font-size: 4.3px; line-height: 1.45; color: var(--ink-soft); }
  .card-back .band { height: 5px; }
</style>
</head>
<body>

<svg width="0" height="0" style="position:absolute">
  <defs>
    <symbol id="icon-phone" viewBox="0 0 10 10"><rect width="10" height="10" rx="1.5"/><path d="M3 2.2l1 1.4-.6.8c.4.9 1 1.5 1.9 1.9l.8-.6 1.4 1-.6 1.2C4.7 7.8 2.2 5.3 1.9 3z" fill="#fff"/></symbol>
    <symbol id="icon-mail" viewBox="0 0 10 10"><rect width="10" height="10" rx="1.5"/><rect x="2" y="3" width="6" height="4" fill="none" stroke="#fff" stroke-width=".8"/><path d="M2 3l3 2.3L8 3" fill="none" stroke="#fff" stroke-width=".8"/></symbol>
    <symbol id="icon-web" viewBox="0 0 10 10"><rect width="10" height="10" rx="1.5"/><circle cx="5" cy="5" r="2.8" fill="none" stroke="#fff" stroke-width=".8"/><path d="M2.2 5h5.6" stroke="#fff" stroke-width=".7"/></symbol>
  </defs>
</svg>

<section class="piece folder" aria-label="Presentation folder">
  <div class="folder-spine"></div>
  <div class="wordmark">Talvora</div>
</section>

<section class="piece letterhead" aria-label="Letterhead">
  <div class="wordmark">Talvora</div>
  <div class="letter-body">
    <p class="salutation">Dear sir,</p>
    <p>Clear communication sits at the heart of every successful compliance program. Whether a question arrives by phone, by email or in person, our advisors answer it with care and precision, and we document every step so that your team always knows where a submission stands and what comes next.</p>
    <p>Regulated industries move quickly, yet written records still carry the greatest weight. Audits, inspections and design reviews all depend on letters and reports that are accurate, complete and easy to follow. We help medical device, pharmaceutical and biotech companies prepare those records with confidence, from the first gap assessment to the final response.</p>
    <p>Every document speaks for the organization that writes it, so we take great care that the language, structure and evidence suit the occasion and the reader.</p>
    <p>Thank you for considering Talvora. We look forward to learning about your goals and to building a plan that fits your products, your timeline and your team.</p>
    <p style="margin-top:12px;margin-bottom:0">Yours Sincerely,</p>
    <p class="sign-name">Lena Marchetti</p>
  </div>
  <div class="signature" role="img" aria-label="Handwritten signature of Lena Marchetti"></div>
  <div class="footer-contacts">
    <span><svg class="icon"><use href="#icon-phone"/></svg>(510) 555-0142</span>
    <span><svg class="icon"><use href="#icon-mail"/></svg>info@talvora-advisory.com</span>
    <span><svg class="icon"><use href="#icon-web"/></svg>www.talvora-advisory.com</span>
    <span class="copyright">© 2015 Talvora, Inc.</span>
  </div>
  <div class="band"><div class="band-grey" style="width:250px"></div><div class="band-blue"></div></div>
</section>

<section class="piece envelope-front" aria-label="Envelope front">
  <div class="wordmark">Talvora</div>
  <div class="return-address">4120 Harbor Point Road Suite 310<br>Oakland, CA 94607</div>
  <div class="band"><div class="band-grey" style="width:298px"></div><div class="band-blue"></div></div>
</section>

<section class="piece envelope-back" aria-label="Envelope back">
  <svg width="465" height="202" viewBox="0 0 465 202">
    <polygon points="0,0 465,0 465,10 400,92 65,92 0,10" fill="var(--brand-blue)"/>
  </svg>
  <div class="wordmark">Talvora</div>
</section>

<section class="piece card-front" aria-label="Business card front">
  <div class="wordmark">Talvora</div>
  <div class="card-url">www.talvora-advisory.com</div>
</section>

<section class="piece card-back" aria-label="Business card back">
  <div class="card-name">JORDAN PELL</div>
  <div class="card-role">Account Executive</div>
  <div class="wordmark">Talvora</div>
  <div class="card-contacts">
    <div><svg class="icon"><use href="#icon-phone"/></svg>(510) 555-0142</div>
    <div><svg class="icon"><use href="#icon-mail"/></svg>info@talvora-advisory.com</div>
    <div><svg class="icon"><use href="#icon-web"/></svg>www.talvora-advisory.com</div>
  </div>
  <div class="card-address">Bay Area HQ<br>4120 Harbor Point Road Suite 310<br>Oakland, CA 94607</div>
  <div class="band"><div class="band-grey" style="width:68px"></div><div class="band-blue"></div></div>
</section>

</body>
</html>
```